Business Card Design

We provide services doing multiple jobs in the construction industry.Please note: The company name needs to be ROCK SOLID BUILDING SERVICESAttached logo was an example of what we wanted. Can you change up the colors?

Industry/Entity Type

Construction

Contact Information for Business Card

ROCK SOLID BUILDING SERVICES5401 HUDSON BEND RDAUSTIN, TX 78734(512)243-6854ROCKSOLIDBUILDINGSERVICES@GMAIL.COM

```html
<!DOCTYPE html>
<html lang="en">
<head>
<meta charset="utf-8">
<title>Pearlwood Framing Works – Business Card</title>
<link rel="stylesheet" href="https://fonts.googleapis.com/css2?family=Arimo:wght@400;700&display=swap">
<style>
  :root {
    --backdrop: #ececec;
    --card: #ffffff;
    --ink: #111111;
    --navy: #2b2a72;
    --teal: #0a9cc4;
    --skyline: #cfcfcf;
  }
  html, body {
    margin: 0;
    width: 1200px;
    height: 864px;
    overflow: hidden;
    background: var(--backdrop);
    font-family: "Arimo", Arial, sans-serif;
  }
  .card {
    position: absolute;
    left: 50px;
    top: 118px;
    width: 1100px;
    height: 628px;
    background: var(--card);
    overflow: hidden;
    box-shadow: 0 6px 24px rgba(0,0,0,0.12);
  }
  .company-name {
    position: absolute;
    left: 64px;
    top: 118px;
    margin: 0;
    font-size: 38px;
    font-weight: 700;
    line-height: 1.05;
    color: var(--ink);
    letter-spacing: 0.5px;
  }
  .brand-mark {
    position: absolute;
    right: 80px;
    top: 70px;
    display: flex;
    align-items: center;
    gap: 14px;
  }
  .brand-mark__square {
    width: 46px;
    height: 46px;
    background: var(--navy);
  }
  .brand-mark__name {
    font-size: 44px;
    font-weight: 700;
    color: var(--navy);
    letter-spacing: 1px;
  }
  .contact-list {
    position: absolute;
    right: 50px;
    top: 300px;
    margin: 0;
    padding: 0;
    list-style: none;
    text-align: right;
    font-size: 24px;
    color: var(--ink);
    line-height: 1.5;
  }
  .contact-list li {
    display: flex;
    justify-content: flex-end;
    align-items: center;
    gap: 14px;
  }
  .contact-icon {
    width: 20px;
    height: 20px;
    flex: none;
  }
  .contact-icon--blank { visibility: hidden; }
  .bottom-art {
    position: absolute;
    left: 0;
    bottom: 0;
    width: 1100px;
    height: 260px;
  }
</style>
</head>
<body>
  <div class="card">
    <h1 class="company-name">PEARLWOOD FRAMING<br>WORKS</h1>

    <div class="brand-mark">
      <span class="brand-mark__square"></span>
      <span class="brand-mark__name">PEARLWOOD</span>
    </div>

    <ul class="contact-list">
      <li>(512)555-0193
        <svg class="contact-icon" viewBox="0 0 24 24"><path fill="#111" d="M6.6 10.8a15.1 15.1 0 0 0 6.6 6.6l2.2-2.2a1 1 0 0 1 1-.25 11.4 11.4 0 0 0 3.6.57 1 1 0 0 1 1 1V20a1 1 0 0 1-1 1A17 17 0 0 1 3 4a1 1 0 0 1 1-1h3.5a1 1 0 0 1 1 1c0 1.25.2 2.45.57 3.6a1 1 0 0 1-.25 1z"/></svg>
      </li>
      <li>7732 FERNGLEN PASS LN AUSTIN, TX 78734
        <svg class="contact-icon" viewBox="0 0 24 24"><path fill="#111" d="M12 2a7 7 0 0 0-7 7c0 5.2 7 13 7 13s7-7.8 7-13a7 7 0 0 0-7-7zm0 9.5A2.5 2.5 0 1 1 12 6.5a2.5 2.5 0 0 1 0 5z"/></svg>
      </li>
      <li>PEARLWOODFRAMINGWORKS@MAILNEST.EXAMPLE
        <svg class="contact-icon" viewBox="0 0 24 24"><path fill="#111" d="M2 5h20v14H2zm2 2v.5l8 5 8-5V7z"/></svg>
      </li>
    </ul>

    <svg class="bottom-art" viewBox="0 0 1100 260" preserveAspectRatio="none">
      <rect class="skyline" role="img" aria-label="City skyline silhouette in light grey" x="0" y="60" width="560" height="200" fill="var(--skyline)"/>
      <path class="wave wave--navy" fill="var(--navy)" d="M0,185 C300,195 560,160 760,90 C880,50 990,40 1100,50 L1100,260 L0,260 Z"/>
      <path class="wave-divider" fill="none" stroke="#fff" stroke-width="5" d="M0,212 C300,220 580,185 780,110 C900,68 1000,60 1100,68"/>
      <path class="wave wave--teal" fill="var(--teal)" d="M0,222 C300,230 590,195 790,120 C905,80 1005,72 1100,78 L1100,260 L0,260 Z"/>
    </svg>
  </div>
</body>
</html>
```